Unique Business Card Design

Unique Business Card design for our orthotic and prosthetic company. Our logo is on our website, color is light blue. Unique shape (artificial leg shaped, vertical, etc..) preferred. Logo, business name, individual name and basic demographics needed.

Industry/Entity Type

Business

Contact Information for Business Card

Logo, Industry, Phone # Logo, "Prosthetic & Orthotic Services" Place to add individual name and contact info

Colors
cee9f5

Requirements
Must have
• The icon must be there, placement of "Prosthetic & Orthotic Services" can be moved
Nice to have
• Like the mix of light blue, and a little darker blue. One design included the icons from my website which was a nice touch

```html
<!DOCTYPE html>
<html lang="en">
<head>
<meta charset="utf-8">
<title>Limbwell Inc – Business Cards</title>
<link rel="stylesheet" href="https://fonts.googleapis.com/css2?family=Lato:wght@400;700;900&family=Libre+Baskerville:ital@1&display=swap">
<style>
  :root {
    --backdrop: #4a4039;
    --card-black: #141414;
    --silver: #b9b9b9;
    --silver-dark: #7d7d7d;
    --brand-blue: #2f6fb8;
    --name-blue: #3a7fd0;
    --text-light: #e6e6e6;
    --divider: #3a3a3a;
  }
  * { margin: 0; padding: 0; box-sizing: border-box; }
  html, body { width: 1200px; height: 864px; overflow: hidden; }
  body {
    background: var(--backdrop);
    font-family: "Lato", Arial, sans-serif;
    display: flex;
    align-items: center;
    justify-content: center;
    gap: 50px;
  }
  .card {
    width: 520px;
    height: 300px;
    background: var(--card-black);
    position: relative;
    box-shadow: 0 14px 30px rgba(0,0,0,.45);
  }

  /* Front */
  .brand-lockup {
    position: absolute;
    top: 70px;
    left: 52px;
    display: flex;
    align-items: center;
    gap: 22px;
  }
  .brand-mark {
    width: 100px; height: 100px; border-radius: 50%;
    background: var(--silver);
    flex: none;
  }
  .brand-name {
    font-weight: 900;
    font-size: 34px;
    color: var(--silver);
    letter-spacing: 1px;
    border-bottom: 2px solid var(--silver-dark);
    padding-bottom: 4px;
  }
  .brand-tagline {
    font-family: "Libre Baskerville", Georgia, serif;
    font-style: italic;
    font-size: 15px;
    color: var(--silver);
    margin-top: 6px;
  }
  .front-web {
    position: absolute;
    left: 0; right: 0; bottom: 52px;
    display: flex; align-items: center; justify-content: center; gap: 16px;
    font-size: 14px; color: var(--silver);
  }
  .front-web .rule { width: 80px; height: 1px; background: var(--silver-dark); }

  /* Back */
  .back-mark {
    position: absolute;
    left: 46px; top: 55px;
    width: 190px; height: 190px; border-radius: 50%;
    background: var(--brand-blue);
  }
  .back-divider {
    position: absolute;
    left: 268px; top: 40px;
    width: 1px; height: 220px;
    background: var(--divider);
  }
  .contact {
    position: absolute;
    left: 288px; top: 44px;
    color: var(--text-light);
  }
  .person-name { font-size: 21px; font-weight: 700; color: var(--name-blue); }
  .person-title { font-size: 13px; color: var(--name-blue); margin-bottom: 10px; letter-spacing: .5px; }
  .address { font-size: 14px; line-height: 1.3; margin-bottom: 6px; }
  .contact-list { list-style: none; font-size: 14px; }
  .contact-list li { display: flex; align-items: center; gap: 8px; height: 21px; }
  .contact-list svg { width: 13px; height: 13px; fill: var(--name-blue); flex: none; }
  .contact-list .plain { padding-left: 21px; }
</style>
</head>
<body>

<section class="card card-front">
  <div class="brand-lockup">
    <div class="brand-mark"></div>
    <div>
      <div class="brand-name">LIMBWELL INC</div>
      <div class="brand-tagline">Prosthetic &amp; Orthotic Services</div>
    </div>
  </div>
  <div class="front-web"><span class="rule"></span>www.limbwellinc.com<span class="rule"></span></div>
</section>

<section class="card card-back">
  <div class="back-mark"></div>
  <div class="back-divider"></div>
  <div class="contact">
    <div class="person-name">Miriam Kalter</div>
    <div class="person-title">CO LPO</div>
    <div class="address">2380 W. 14th St.<br>Queens, NY 11357</div>
    <ul class="contact-list">
      <li><svg viewBox="0 0 16 16"><path d="M3 1h3l1 4-2 1a9 9 0 0 0 5 5l1-2 4 1v3a2 2 0 0 1-2 2A13 13 0 0 1 1 3a2 2 0 0 1 2-2z"/></svg>555.201.1700</li>
      <li><svg viewBox="0 0 16 16"><path d="M4 0h8a1 1 0 0 1 1 1v14a1 1 0 0 1-1 1H4a1 1 0 0 1-1-1V1a1 1 0 0 1 1-1zm1 2v10h6V2z"/></svg>555.201.3919</li>
      <li><svg viewBox="0 0 16 16"><path d="M4 1h8v4H4zM1 6h14v7h-3v2H4v-2H1zm4 5v2h6v-2z"/></svg>555-0145</li>
      <li><svg viewBox="0 0 16 16"><path d="M0 3h16v10H0zm1 1 7 5 7-5z"/></svg>mkalter@limbwellinc.com</li>
      <li><svg viewBox="0 0 16 16"><circle cx="8" cy="8" r="8"/></svg>www.limbwellinc.com</li>
    </ul>
  </div>
</section>

</body>
</html>
```